Quill Physical Therapy Website

I would need a clean modern website built to showcase my Physical therapy brand and services. I would need a simple but descriptive website that can ultimately connect my patients to my electronic medical portal so they may book an appointment..

```html
<!DOCTYPE html>
<html lang="en">
<head>
<meta charset="utf-8">
<title>Quill Physical Therapy</title>
<link href="https://fonts.googleapis.com/css2?family=Playfair+Display:wght@400;700&family=Roboto:wght@400;500;700&display=swap" rel="stylesheet">
<style>
:root{
  --teal:#1f6f6e;
  --teal-dark:#0f4c4b;
  --teal-deep:#0b3b3b;
  --ink:#1c1c1c;
  --muted:#6b6b6b;
  --paper:#ffffff;
  --mist:#f1f2f2;
  --footer:#0c0c0c;
  --star:#f2b01e;
}
*{box-sizing:border-box;margin:0;padding:0}
html,body{width:1200px;height:3960px;overflow:hidden}
body{font-family:"Roboto",Arial,sans-serif;color:var(--ink);background:var(--paper);position:relative}
.serif{font-family:"Playfair Display",Georgia,serif}
a{color:inherit;text-decoration:none}

/* header */
.topbar{height:80px;display:flex;align-items:center;justify-content:space-between;padding:0 40px;background:var(--paper)}
.brand{display:flex;align-items:center;gap:14px}
.brand-dot{width:44px;height:44px;border-radius:50%;background:var(--teal)}
.brand-name{font-family:"Roboto",Arial,sans-serif;font-weight:700;font-size:30px;color:var(--teal);letter-spacing:2px}
.top-actions{display:flex;gap:16px}
.btn-consult{background:var(--teal);color:#fff;font-size:14px;font-weight:500;padding:12px 22px;letter-spacing:.5px}
.btn-phone{border:2px solid var(--teal);color:var(--teal);font-size:14px;font-weight:700;padding:10px 22px;border-radius:22px;display:flex;align-items:center;gap:8px}
.nav{height:40px;background:var(--teal);display:flex;justify-content:center;align-items:center;gap:40px;padding-left:120px}
.nav a{color:#fff;font-size:13px;font-weight:500;letter-spacing:.5px}

/* hero */
.hero{position:relative;height:612px;background:linear-gradient(110deg,#5f6b6c 0%,#a9b4b3 35%,#d8dedc 60%,#8b9593 100%)}
.hero-shade{position:absolute;inset:0;background:linear-gradient(90deg,rgba(10,30,30,.55) 0%,rgba(10,30,30,.15) 45%,rgba(0,0,0,0) 70%)}
.hero-copy{position:absolute;left:40px;top:300px;color:#fff}
.hero-title{font-size:58px;line-height:1.05;font-weight:400;letter-spacing:1px}
.btn-outline-light{display:inline-block;margin-top:26px;border:2px solid #fff;color:#fff;font-size:14px;font-weight:500;padding:12px 20px;letter-spacing:.5px}
.hero-dots{position:absolute;bottom:28px;left:50%;transform:translateX(-50%);display:flex;gap:10px}
.hero-dots span{width:10px;height:10px;border-radius:50%;background:rgba(255,255,255,.6)}
.hero-dots span.on{background:#fff}

/* welcome */
.welcome{height:548px;position:relative}
.welcome-copy{position:absolute;left:112px;top:104px;width:470px}
.welcome-title{font-size:40px;line-height:1.1;font-weight:400;color:var(--ink)}
.welcome-title .accent{color:var(--teal)}
.body-text{font-size:14px;line-height:1.7;color:var(--muted);margin-top:22px}
.btn-solid{display:inline-block;background:var(--teal);color:#fff;font-size:13px;font-weight:500;padding:13px 22px;letter-spacing:.5px;margin-top:28px}
.welcome-photo{position:absolute;left:632px;top:88px;width:456px;height:368px;background:linear-gradient(135deg,#cfd8d6,#e9edec 50%,#a7bdb9)}

/* specialties */
.specialties{height:560px;background:var(--mist);padding-top:54px;text-align:center}
.eyebrow{font-size:15px;font-weight:500;color:var(--teal);letter-spacing:1px}
.section-title{font-size:36px;font-weight:400;color:var(--ink);margin-top:4px}
.cards{display:flex;justify-content:center;gap:24px;margin-top:38px}
.card{width:300px;height:356px;background:#fff;box-shadow:0 2px 8px rgba(0,0,0,.08);position:relative}
.card-photo{height:192px}
.card-icon{position:absolute;left:50%;top:164px;transform:translateX(-50%);width:58px;height:58px;border-radius:50%;background:#fff;border:2px solid var(--teal);display:flex;align-items:center;justify-content:center}
.card-title{margin-top:50px;font-size:24px;font-weight:400}
.card-text{font-size:13px;line-height:1.6;color:var(--muted);padding:12px 28px 0}

/* testimonials */
.testimonials{height:340px;margin-top:40px;position:relative;background:linear-gradient(180deg,var(--teal) 0%,var(--teal-dark) 60%,var(--teal-deep) 100%);text-align:center;color:#fff;padding-top:48px;overflow:hidden}
.testimonials .eyebrow{color:#fff}
.testimonials .section-title{color:#fff}
.ridge{position:absolute;left:0;bottom:0;width:1200px;height:200px}
.quotes{position:relative;display:flex;justify-content:center;gap:32px;margin-top:34px}
.quote{width:448px;height:140px;background:#fff;color:var(--ink);text-align:left;padding:18px 22px}
.stars{color:var(--star);font-size:14px;letter-spacing:2px}
.quote-text{font-size:13px;line-height:1.6;color:var(--muted);margin-top:6px}
.quote-name{font-size:13px;font-weight:700;margin-top:8px}
.arrow{position:absolute;top:200px}
.arrow.left{left:90px}
.arrow.right{right:90px}

/* news */
.news{height:600px;text-align:center;padding-top:74px}
.news-grid{display:flex;justify-content:center;gap:36px;margin-top:40px;text-align:left}
.post{width:300px}
.post-photo{height:208px}
.post-title{font-size:16px;font-weight:700;margin-top:20px}
.post-text{font-size:13px;line-height:1.6;color:var(--muted);margin-top:8px}
.read-more{display:inline-block;font-size:12px;font-weight:700;color:var(--ink);margin-top:12px;letter-spacing:.5px}

/* therapist */
.therapist{height:640px;position:relative;background:linear-gradient(180deg,#fff 0%,#fff 55%,#e6ebea 75%,#9aa8a6 100%)}
.therapist-photo{position:absolute;left:120px;top:40px;width:480px;height:400px;background:linear-gradient(135deg,#e9ecec,#c9d4d6 55%,#6f8ea6)}
.forest{position:absolute;left:0;bottom:0;width:1200px;height:220px}
.therapist-copy{position:absolute;left:644px;top:96px;width:440px}
.therapist-title{font-size:32px;line-height:1.15;font-weight:400;margin-top:8px}
.btn-row{display:flex;gap:14px;margin-top:24px}
.btn-row .btn-solid{margin-top:0}
.btn-ghost{border:2px solid var(--teal);color:var(--teal);font-size:13px;font-weight:500;padding:11px 20px;letter-spacing:.5px}

/* footer */
.footer{position:absolute;left:0;top:3540px;width:1200px;height:420px;background:var(--footer);color:#fff}
.footer-inner{display:flex;padding:80px 0 0 120px}
.footer-brand{width:220px;display:flex;align-items:center;gap:12px;height:170px}
.footer-brand .brand-dot{background:#fff;width:40px;height:40px}
.footer-brand .brand-name{color:#fff;font-size:28px}
.footer-col{margin-right:60px}
.footer-col h4{font-size:16px;font-weight:700;letter-spacing:1px;margin-bottom:14px}
.footer-col li{list-style:none;font-size:13px;line-height:1.75;color:#d6d6d6}
.contact-line{display:flex;gap:10px;align-items:flex-start;font-size:13px;color:#d6d6d6;margin-bottom:12px;line-height:1.5}
.newsletter{width:310px}
.email-field{height:48px;border:1px solid #555;background:#111;color:#aaa;font-size:13px;padding:15px 14px}
.btn-sub{display:block;background:var(--teal);color:#fff;text-align:center;font-size:13px;font-weight:700;padding:16px 0;margin-top:10px;letter-spacing:.5px}
.socials{display:flex;gap:14px;margin-top:20px;padding-left:50px}
.socials span{width:36px;height:36px;border-radius:50%;background:var(--teal)}
.copyright{position:absolute;left:0;bottom:0;width:1200px;height:50px;border-top:1px solid #2a2a2a;display:flex;align-items:center;justify-content:center;font-size:12px;color:#bdbdbd}
</style>
</head>
<body>

<header>
  <div class="topbar">
    <div class="brand"><span class="brand-dot"></span><span class="brand-name">QUILL</span></div>
    <div class="top-actions">
      <a class="btn-consult" href="#">REQUEST A CONSULTATION</a>
      <a class="btn-phone" href="#">
        <svg width="14" height="14" viewBox="0 0 24 24"><path fill="#1f6f6e" d="M6.6 10.8a15.1 15.1 0 0 0 6.6 6.6l2.2-2.2a1 1 0 0 1 1-.25c1.1.37 2.3.57 3.6.57a1 1 0 0 1 1 1V20a1 1 0 0 1-1 1A17 17 0 0 1 3 4a1 1 0 0 1 1-1h3.5a1 1 0 0 1 1 1c0 1.25.2 2.45.57 3.57a1 1 0 0 1-.25 1z"/></svg>
        (555) 555-5555</a>
    </div>
  </div>
  <nav class="nav">
    <a href="#">ABOUT ▾</a><a href="#">PROGRAMS ▾</a><a href="#">FACILITIES</a><a href="#">FAQS</a><a href="#">CAREERS</a><a href="#">CONTACT</a><a href="#">PATIENT FORM</a>
  </nav>
</header>

<section class="hero">
  <div role="img" aria-label="Therapist stretching a patient's leg on a treatment table in a bright clinic" style="position:absolute;inset:0"></div>
  <div class="hero-shade"></div>
  <div class="hero-copy">
    <h1 class="hero-title serif">QUILL PHYSICAL<br>THERAPY</h1>
    <a class="btn-outline-light" href="#">SCHEDULE AN APPOINTMENT</a>
  </div>
  <div class="hero-dots"><span class="on"></span><span></span><span></span></div>
</section>

<section class="welcome">
  <div class="welcome-copy">
    <h2 class="welcome-title serif">WELCOME TO<br><span class="accent">QUILL PHYSICAL THERAPY</span></h2>
    <p class="body-text">Sed ut perspiciatis unde omnis iste natus error sit voluptatem accusantium doloremque laudantium, totam rem aperiam, eaque ipsa quae ab illo inventore veritatis et quasi architecto beatae vitae dicta sunt explicabo. Nemo enim ipsam voluptatem quia voluptas sit aspernatur aut odit aut fugit.</p>
    <a class="btn-solid" href="#">LEARN MORE</a>
  </div>
  <div class="welcome-photo" role="img" aria-label="Therapist guiding a patient through a balance exercise in the gym"></div>
</section>

<section class="specialties">
  <p class="eyebrow">WHAT WE PROVIDE</p>
  <h2 class="section-title serif">AREAS OF SPECIALTY ARE</h2>
  <div class="cards">
    <article class="card">
      <div class="card-photo" role="img" aria-label="Hands-on shoulder therapy session" style="background:linear-gradient(135deg,#b89a85,#e2d3c8)"></div>
      <div class="card-icon"><svg width="28" height="28" viewBox="0 0 24 24" fill="none" stroke="#1f6f6e" stroke-width="2"><circle cx="12" cy="5" r="2.5"/><path d="M12 8v7M7 11h10M9 21l3-6 3 6"/></svg></div>
      <h3 class="card-title serif">FINIBUS BONORUM</h3>
      <p class="card-text">Sed ut perspiciatis unde omnis iste natus error sit voluptatem accusantium doloremque laudantium, totam rem aperiam.</p>
    </article>
    <article class="card">
      <div class="card-photo" role="img" aria-label="Therapist assisting an older patient with arm exercise" style="background:linear-gradient(135deg,#8fb3b6,#dfe7e4)"></div>
      <div class="card-icon"><svg width="28" height="28" viewBox="0 0 24 24" fill="none" stroke="#1f6f6e" stroke-width="2"><rect x="4" y="9" width="16" height="6" rx="1"/><path d="M2 12h2M20 12h2M8 9V6M16 9V6"/></svg></div>
      <h3 class="card-title serif">FINIBUS BONORUM</h3>
      <p class="card-text">Sed ut perspiciatis unde omnis iste natus error sit voluptatem accusantium doloremque laudantium, totam rem aperiam.</p>
    </article>
    <article class="card">
      <div class="card-photo" role="img" aria-label="Therapist working with a patient on an exercise ball" style="background:linear-gradient(135deg,#6f9bb0,#d7e0e4)"></div>
      <div class="card-icon"><svg width="28" height="28" viewBox="0 0 24 24" fill="none" stroke="#1f6f6e" stroke-width="2"><circle cx="12" cy="12" r="8"/><path d="M8 12h8M12 8v8"/></svg></div>
      <h3 class="card-title serif">FINIBUS BONORUM</h3>
      <p class="card-text">Sed ut perspiciatis unde omnis iste natus error sit voluptatem accusantium doloremque laudantium, totam rem aperiam.</p>
    </article>
  </div>
</section>

<section class="testimonials">
  <svg class="ridge" viewBox="0 0 1200 200" preserveAspectRatio="none" aria-hidden="true"><path d="M0 140 L180 70 L330 130 L520 50 L700 120 L880 60 L1050 115 L1200 80 L1200 200 L0 200Z" fill="#0a3434" opacity=".55"/></svg>
  <p class="eyebrow" style="position:relative">TESTIMONIALS</p>
  <h2 class="section-title serif" style="position:relative">WHAT PEOPLE ARE SAYING</h2>
  <div class="quotes">
    <blockquote class="quote">
      <div class="stars">★★★★★</div>
      <p class="quote-text">Sed ut perspiciatis unde omnis iste natus error sit voluptatem accusantium doloremque laudantium, totam rem aperiam, eaque ipsa quae ab illo inventore.</p>
      <p class="quote-name">Jordan Reyes – 06/28/18</p>
    </blockquote>
    <blockquote class="quote">
      <div class="stars">★★★★★</div>
      <p class="quote-text">Sed ut perspiciatis unde omnis iste natus error sit voluptatem accusantium doloremque laudantium, totam rem aperiam, eaque ipsa quae ab illo inventore.</p>
      <p class="quote-name">Jordan Reyes – 06/28/18</p>
    </blockquote>
  </div>
  <svg class="arrow left" width="26" height="20" viewBox="0 0 26 20"><path d="M24 10H3M10 2 2 10l8 8" fill="none" stroke="#fff" stroke-width="2"/></svg>
  <svg class="arrow right" width="26" height="20" viewBox="0 0 26 20"><path d="M2 10h21M16 2l8 8-8 8" fill="none" stroke="#fff" stroke-width="2"/></svg>
</section>

<section class="news">
  <p class="eyebrow">UPDATES</p>
  <h2 class="section-title serif">LATEST NEWS</h2>
  <div class="news-grid">
    <article class="post">
      <div class="post-photo" role="img" aria-label="Smiling therapist in a clinic hallway" style="background:linear-gradient(135deg,#c9b7a9,#eee7e1)"></div>
      <h3 class="post-title">The standard Lorem passage, used</h3>
      <p class="post-text">Sed ut perspiciatis unde omnis iste natus error sit voluptatem accusantium doloremque laudantium, totam rem aperiam, eaque ipsa.</p>
      <a class="read-more" href="#">READ MORE</a>
    </article>
    <article class="post">
      <div class="post-photo" role="img" aria-label="Patient doing a lying stretch with therapist support" style="background:linear-gradient(135deg,#5d7f9e,#cdd8e2)"></div>
      <h3 class="post-title">The standard Lorem passage, used</h3>
      <p class="post-text">Sed ut perspiciatis unde omnis iste natus error sit voluptatem accusantium doloremque laudantium, totam rem aperiam, eaque ipsa.</p>
      <a class="read-more" href="#">READ MORE</a>
    </article>
    <article class="post">
      <div class="post-photo" role="img" aria-label="Knee mobility treatment on a table" style="background:linear-gradient(135deg,#8f7a6c,#e3dad3)"></div>
      <h3 class="post-title">The standard Lorem passage, used</h3>
      <p class="post-text">Sed ut perspiciatis unde omnis iste natus error sit voluptatem accusantium doloremque laudantium, totam rem aperiam, eaque ipsa.</p>
      <a class="read-more" href="#">READ MORE</a>
    </article>
  </div>
</section>

<section class="therapist">
  <svg class="forest" viewBox="0 0 1200 220" preserveAspectRatio="none" role="img" aria-label="Misty pine forest"><defs><linearGradient id="fog" x1="0" y1="0" x2="0" y2="1"><stop offset="0" stop-color="#c3cdcc" stop-opacity="0"/><stop offset="1" stop-color="#53625f"/></linearGradient></defs><rect width="1200" height="220" fill="url(#fog)"/></svg>
  <div class="therapist-photo" role="img" aria-label="Therapist in white coat beside treatment tables"></div>
  <div class="therapist-copy">
    <p class="eyebrow">BECOME A THERAPIST</p>
    <h2 class="therapist-title serif">WANT TO SUPERVISION,<br>INTERNS, CONSULTING.</h2>
    <p class="body-text">Lorem ipsum dolor sit amet, consectetur adipiscing elit. Ut elit tellus, luctus nec ullamcorper mattis, pulvinar dapibus leo. Sed ut perspiciatis unde omnis iste natus error sit voluptatem accusantium doloremque laudantium, totam rem aperiam.</p>
    <div class="btn-row">
      <a class="btn-solid" href="#">BOOK A SESSION</a>
      <a class="btn-ghost" href="#">JOIN OUR COMMUNITY</a>
    </div>
  </div>
</section>

<footer class="footer">
  <div class="footer-inner">
    <div class="footer-brand"><span class="brand-dot"></span><span class="brand-name">QUILL</span></div>
    <div class="footer-col">
      <h4>EXPLORE</h4>
      <ul><li>Home</li><li>About</li><li>Programs</li><li>Facilities</li><li>FAQs</li><li>Careers</li><li>Contact</li><li>Patient Forms</li></ul>
    </div>
    <div class="footer-col" style="width:260px">
      <h4>CONTACT US</h4>
      <div class="contact-line"><svg width="14" height="16" viewBox="0 0 24 24"><path fill="#fff" d="M12 2a7 7 0 0 0-7 7c0 5 7 13 7 13s7-8 7-13a7 7 0 0 0-7-7zm0 9.5A2.5 2.5 0 1 1 12 6.5a2.5 2.5 0 0 1 0 5z"/></svg><span>1420 Harbor Lane,<br>Springfield 40715</span></div>
      <div class="contact-line"><svg width="14" height="14" viewBox="0 0 24 24"><path fill="#fff" d="M6.6 10.8a15.1 15.1 0 0 0 6.6 6.6l2.2-2.2a1 1 0 0 1 1-.25c1.1.37 2.3.57 3.6.57a1 1 0 0 1 1 1V20a1 1 0 0 1-1 1A17 17 0 0 1 3 4a1 1 0 0 1 1-1h3.5a1 1 0 0 1 1 1c0 1.25.2 2.45.57 3.57a1 1 0 0 1-.25 1z"/></svg><span>(555) 555-5555</span></div>
      <div class="contact-line"><svg width="14" height="12" viewBox="0 0 24 18"><rect x="1" y="1" width="22" height="16" fill="none" stroke="#fff" stroke-width="2"/><path d="M1 1l11 9 11-9" fill="none" stroke="#fff" stroke-width="2"/></svg><span>info@quillphysicaltherapy.com</span></div>
    </div>
    <div class="newsletter">
      <h4 style="font-size:16px;font-weight:700;letter-spacing:1px;margin-bottom:14px">SIGN UP FOR NEWSLETTER</h4>
      <div class="email-field">Email..</div>
      <a class="btn-sub" href="#">SUBSCRIBE</a>
      <div class="socials"><span></span><span></span><span></span><span></span></div>
    </div>
  </div>
  <div class="copyright">Copyright © 1999-2021 Quill Physical Therapy. All rights reserved.</div>
</footer>

</body>
</html>
```